Updated DJ business Card showing other businesses

DJ Talbo offers professional mobile dj services including DJ. MC. Karaoke.
Silent Disco (will attach logo)
I also offer a 360 Photo Booth.

Contact info:
(405) 555-0147
mark.fenstell@pelimail.com
Social Media @DJTalboOKC

```html
<!DOCTYPE html>
<html lang="en">
<head>
<meta charset="utf-8">
<title>DJ Talbo Business Card</title>
<link rel="stylesheet" href="https://fonts.googleapis.com/css2?family=Poppins:wght@500;700&display=swap">
<style>
  :root {
    --stage: #2e2e30;
    --pink: #d42049;
    --black: #111111;
    --white: #ffffff;
    --yellow: #f3ee1f;
    --ink: #2a2a2a;
    --purple: #5a2b78;
    --magenta: #b2338f;
  }
  * { margin: 0; padding: 0; box-sizing: border-box; }
  html, body {
    width: 1200px; height: 998px; overflow: hidden;
    background: var(--stage);
    font-family: "Poppins", sans-serif;
  }
  .canvas {
    width: 1200px; height: 998px;
    display: flex; flex-direction: column; align-items: center; justify-content: center;
    gap: 40px;
  }
  .card {
    width: 760px; height: 434px; position: relative; overflow: hidden;
    box-shadow: 0 10px 30px rgba(0,0,0,.45);
  }
  /* Front */
  .card-front {
    background: var(--pink);
    display: flex; align-items: center; justify-content: center;
  }
  .brand-name {
    font-weight: 700; line-height: 1;
    color: var(--black);
  }
  .card-front .brand-name { font-size: 64px; }
  /* Back */
  .card-back { color: var(--white); }
  .back-photo {
    position: absolute; inset: 0;
    background:
      radial-gradient(circle at 22% 75%, rgba(40,160,70,.55), transparent 22%),
      radial-gradient(circle at 80% 30%, rgba(70,110,230,.45), transparent 30%),
      linear-gradient(135deg, var(--magenta) 0%, var(--purple) 45%, #3a2150 70%, #7a3d8f 100%);
  }
  .back-glow {
    position: absolute; left: 0; right: 0; bottom: 0; height: 45%;
    background: linear-gradient(to bottom, rgba(243,238,31,0) 0%, rgba(243,238,31,.85) 55%, var(--yellow) 100%);
  }
  .back-content {
    position: relative; height: 100%;
    display: flex; flex-direction: column; align-items: center;
    padding-top: 28px; text-align: center;
  }
  .dj-name { font-weight: 700; font-size: 64px; line-height: 1; color: var(--white); }
  .services-intro { margin-top: 14px; font-weight: 700; font-size: 22px; color: var(--yellow); }
  .services-list { margin-top: 4px; font-weight: 700; font-size: 38px; color: var(--white); }
  .photo-booth {
    margin-top: 14px; width: 570px; padding: 10px 0;
    background: var(--pink); border-radius: 30px;
    font-weight: 700; font-size: 28px; color: var(--white);
  }
  .back-footer {
    position: absolute; left: 40px; right: 40px; bottom: 26px;
    display: flex; align-items: flex-end; justify-content: space-between;
  }
  .back-footer .brand-name { font-size: 32px; padding-bottom: 4px; }
  .contact { list-style: none; color: var(--ink); font-weight: 500; font-size: 17px; line-height: 1.55; }
  .contact li { display: flex; align-items: center; gap: 8px; }
  .contact svg { width: 16px; height: 16px; fill: var(--ink); }
</style>
</head>
<body>
<main class="canvas">
  <section class="card card-front">
    <p class="brand-name">Silent Disco</p>
  </section>

  <section class="card card-back">
    <div class="back-photo" role="img" aria-label="Blurred photo of a DJ's hand on mixing decks under purple and pink club lights"></div>
    <div class="back-glow"></div>
    <div class="back-content">
      <h1 class="dj-name">DJ Talbo</h1>
      <p class="services-intro">offers professiona Mobile Dj Services including</p>
      <p class="services-list">DJ. MC. Karaoke</p>
      <p class="photo-booth">I also offer a 360 Photo Booth.</p>
    </div>
    <div class="back-footer">
      <p class="brand-name">Silent Disco</p>
      <ul class="contact">
        <li><svg viewBox="0 0 24 24" aria-hidden="true"><path d="M6.6 10.8a15 15 0 0 0 6.6 6.6l2.2-2.2a1 1 0 0 1 1-.25 11.4 11.4 0 0 0 3.6.57 1 1 0 0 1 1 1V20a1 1 0 0 1-1 1A17 17 0 0 1 3 4a1 1 0 0 1 1-1h3.5a1 1 0 0 1 1 1c0 1.25.2 2.45.57 3.57a1 1 0 0 1-.25 1z"/></svg>(405) 555-0147</li>
        <li><svg viewBox="0 0 24 24" aria-hidden="true"><path d="M2 5h20v14H2z M2 5l10 8 10-8" stroke="#f3ee1f" stroke-width="1.5"/></svg>mark.fenstell@pelimail.com</li>
        <li>Social Media @DJTalboOKC</li>
      </ul>
    </div>
  </section>
</main>
</body>
</html>
```